Clinic for cellulit and fat removal

Name of clinic :
Lirava
- Body & Health (this has to be written on the site.)
I need CMS for me to be able to make changes myself.
A webpage for woman searching for a solution to remove fat and cellulit.
The owner is a brazilian woman in Denmark, and want her sense of aestetic shines thru the website.
There needs to be a slide show on the landing page showing big sliding pictures, of the clinic and and the treatments.
The Cryolipolysis, is a treatment freezing fat and cellulit, and this treatment will be the Attraction of the clinic.
Needs These pages in a horisontal fasion. (written in Danish)
Lirava
Behandlinger
- Cryolipolysis
- Trimflox
- Lymfemassage
- Korathelix
- Amberline Tide
Produkter
Priser
Kontakt
Clinic
Coded - Design and coding required
5+ page

```html
<!DOCTYPE html>
<html lang="da">
<head>
<meta charset="utf-8">
<title>Lirava – Body &amp; Health</title>
<link rel="stylesheet" href="https://fonts.googleapis.com/css2?family=Jost:wght@300;400;500&family=Open+Sans:ital,wght@0,400;0,600;1,400&display=swap">
<style>
:root{
  --ink:#2a2a2a;
  --body:#555;
  --muted:#777;
  --nav:#2d2d2d;
  --teal:#8ccfb4;
  --teal-dark:#6fbfa0;
  --green:#4d7f3a;
  --green-btn:#4a7a35;
  --magenta:#b02577;
  --pink:#c2307f;
  --grey-band:#f1f1f1;
  --footer:#f5f5f5;
  --line:#dcdcdc;
}
*{box-sizing:border-box;margin:0;padding:0}
html,body{width:1200px;height:2817px;overflow:hidden}
body{position:relative;background:#fff;font-family:"Open Sans",Arial,sans-serif;color:var(--body)}
.abs{position:absolute}
h1,h2,h3,h4{font-family:"Jost","Futura",sans-serif;font-weight:400;color:var(--ink)}

/* header */
.brand{left:98px;top:22px;display:flex;align-items:center;gap:14px}
.brand-dot{width:22px;height:22px;border-radius:50%;background:var(--teal)}
.brand-name{font-family:"Jost",sans-serif;font-weight:400;font-size:46px;color:var(--ink);line-height:1}
.brand-tag{left:136px;top:78px;font-family:"Open Sans",sans-serif;font-style:italic;font-weight:600;font-size:17px;color:var(--pink)}
.search{left:725px;top:45px;width:233px;height:36px;border:1px solid #bbb;border-radius:3px;font-size:11px;color:#333;padding:10px 10px}
.search svg{position:absolute;right:10px;top:10px}
.lang{left:992px;top:56px;font-size:15px;color:#555}
.lang span{color:var(--green)}

.nav{left:0;top:131px;width:1200px;height:51px;background:var(--nav)}
.nav a{position:absolute;top:0;height:51px;line-height:51px;color:#fff;font-size:17px;text-decoration:none}
.nav .active{background:var(--teal);padding:0 30px;left:100px}
.nav .sep{position:absolute;top:0;width:1px;height:51px;background:#444}

/* hero */
.hero{left:0;top:182px;width:1200px;height:528px;background:radial-gradient(circle at 70% 30%,#eef6d8 0%,#cfe5a8 40%,#9fc77a 100%);overflow:hidden}
.hero-photo{left:30px;top:0;width:560px;height:480px;background:linear-gradient(160deg,#b98462,#7a4a32 60%,#5a5f55)}
.hero-title{left:727px;top:318px;font-size:45px;color:#2b2b2b}
.hero-text{left:729px;top:378px;width:320px;font-size:13.5px;line-height:22px;color:#333}
.btn{display:inline-block;color:#fff;font-size:13px;font-weight:600;text-align:center}
.hero-btn{left:727px;top:466px;width:114px;height:37px;line-height:37px;background:var(--green-btn);border-radius:2px}
.arrow{width:34px;height:34px;border-radius:50%;background:rgba(60,60,60,.7)}
.arrow svg{position:absolute;left:10px;top:9px}

/* treatments */
.sec-title{width:1200px;text-align:center;font-size:36px}
.sec-lead{left:270px;width:660px;text-align:center;font-size:12px;line-height:21px;color:#555}
.treat{width:250px;text-align:center}
.treat-img{position:absolute;left:27px;top:0;width:196px;height:196px;border-radius:50%;border:2px solid #5d8f48}
.treat-badge{position:absolute;left:106px;top:178px;width:38px;height:38px;border-radius:50%;background:var(--green);border:3px solid #fff}
.treat-badge svg{position:absolute;left:8px;top:8px}
.treat h3{position:absolute;top:226px;width:250px;font-size:19px}
.treat p{position:absolute;top:258px;left:10px;width:230px;font-size:12px;line-height:20px;color:#666}

/* welcome */
.welcome{left:0;top:1300px;width:1200px;height:424px;background:var(--grey-band);border-top:1px solid #e4e4e4;border-bottom:1px solid #e4e4e4}
.welcome-photo{left:155px;top:0;width:330px;height:424px;background:linear-gradient(180deg,#f1e2d8,#e9cfc0 55%,#f3f3f3)}
.welcome h2{left:610px;top:82px;font-size:40px}
.welcome p{left:610px;width:480px;font-size:12px;line-height:22px;color:#555}
.welcome .btn{left:612px;top:308px;width:100px;height:32px;line-height:32px;background:var(--magenta);font-size:12px}

/* news */
.news-title{left:98px;top:1786px;font-size:32px;font-weight:300}
.news-nav{left:1077px;top:1800px}
.news-item{width:500px;height:230px}
.news-img{position:absolute;left:0;top:0;width:190px;height:190px;border-radius:50%;border:6px solid #eee;box-shadow:0 2px 6px rgba(0,0,0,.15)}
.news-item h4{position:absolute;left:214px;top:6px;font-size:18px;color:#444}
.news-date{position:absolute;left:214px;top:44px;font-size:12px;font-style:italic;color:var(--magenta)}
.news-item p{position:absolute;left:214px;top:70px;width:290px;font-size:12px;line-height:21px;color:#555}
.news-more{position:absolute;left:214px;top:168px;font-size:13px;color:#333}

/* before after */
.ba{left:0;top:2118px;width:1200px;height:337px;background:var(--teal)}
.ba h2{position:absolute;top:52px;width:1200px;text-align:center;color:#fff;font-size:36px;font-weight:300}
.ba-card{position:absolute;top:124px;width:238px;height:139px;border:4px solid #fff;box-shadow:0 14px 10px -8px rgba(0,0,0,.3)}

/* footer */
.footer{left:0;top:2455px;width:1200px;height:311px;background:var(--footer)}
.footer h4{position:absolute;top:60px;font-size:22px;color:#333}
.f-brand{left:98px;top:78px;display:flex;align-items:center;gap:12px}
.f-tag{left:134px;top:130px;font-style:italic;font-weight:600;font-size:15px;color:var(--pink)}
.social{left:98px;top:178px;display:flex;gap:6px}
.social i{width:22px;height:22px;border-radius:50%;border:1px solid #888;display:block}
.links{left:329px;top:100px;list-style:none}
.links li{font-size:12px;line-height:22.5px;color:#444;padding-left:18px;position:relative}
.links li::before{content:"";position:absolute;left:0;top:8px;width:7px;height:7px;border-radius:50%;background:var(--teal-dark)}
.news-lead{left:537px;top:106px;width:300px;font-size:12px;line-height:20px;color:#555}
.field{left:537px;width:291px;height:42px;background:#fff;border:1px solid #e6e6e6;font-size:11px;color:#555;padding:13px 14px}
.subscribe{left:732px;top:2667px;width:96px;height:42px;line-height:42px;background:var(--teal);color:#fff;font-size:12px;text-align:center}
.contact{left:898px;top:102px;font-size:13px;line-height:22px;color:#555}
.contact-row{position:absolute;left:898px;font-size:13px;color:#444;display:flex;align-items:center;gap:12px}
.bottom{left:0;top:2766px;width:1200px;height:51px;border-top:1px solid var(--line);text-align:center;line-height:51px;font-size:11px;color:#444}
</style>
</head>
<body>

<header>
  <div class="abs brand"><span class="brand-dot"></span><span class="brand-name">Lirava</span></div>
  <div class="abs brand-tag">Body &amp; Health</div>
  <div class="abs search">SEARCH
    <svg width="14" height="14" viewBox="0 0 14 14"><circle cx="6" cy="6" r="4.5" fill="none" stroke="#333" stroke-width="1.8"/><line x1="9.5" y1="9.5" x2="13" y2="13" stroke="#333" stroke-width="2"/></svg>
  </div>
  <div class="abs lang">Danish | <span>English</span></div>
</header>

<nav class="abs nav">
  <a class="active" href="#">Home</a>
  <a href="#" style="left:255px">Lirava</a>
  <span class="sep" style="left:333px"></span>
  <a href="#" style="left:366px">Behandlinger</a>
  <span class="sep" style="left:495px"></span>
  <a href="#" style="left:530px">Produkter</a>
  <span class="sep" style="left:630px"></span>
  <a href="#" style="left:663px">Priser</a>
  <span class="sep" style="left:734px"></span>
  <a href="#" style="left:764px">Kontakt</a>
  <span class="sep" style="left:858px"></span>
</nav>

<section class="abs hero">
  <div class="abs hero-photo" role="img" aria-label="Slide photo: fit man with a green towel eating a fresh salad"></div>
  <svg class="abs" style="left:0;top:420px" width="1200" height="108" viewBox="0 0 1200 108">
    <path d="M0 80 C300 20 700 -10 1200 100 L1200 108 L0 108 Z" fill="#fff"/>
    <path d="M0 78 C300 18 700 -12 1200 98" fill="none" stroke="#4d7f3a" stroke-width="5"/>
    <path d="M600 30 C850 20 1050 50 1200 85" fill="none" stroke="#5d8f48" stroke-width="10" opacity=".8"/>
  </svg>
  <h1 class="abs hero-title">Frys Fedtet Væk</h1>
  <p class="abs hero-text">The Cryolipolysis, is a treatment freezing fat and cellulit, and this treatment will be the Attraction of the clinic</p>
  <a class="abs btn hero-btn" href="#">READ MORE</a>
  <div class="abs arrow" style="left:30px;top:226px"><svg width="14" height="16" viewBox="0 0 14 16"><path d="M10 2 L4 8 L10 14" fill="none" stroke="#fff" stroke-width="2.5"/></svg></div>
  <div class="abs arrow" style="left:1134px;top:226px"><svg width="14" height="16" viewBox="0 0 14 16"><path d="M4 2 L10 8 L4 14" fill="none" stroke="#fff" stroke-width="2.5"/></svg></div>
</section>

<section>
  <h2 class="abs sec-title" style="top:752px">Behandlinger</h2>
  <p class="abs sec-lead" style="top:812px">Sed ut perspiciatis unde omnis iste natus error sit voluptatem accusantium doloremque laudantium, totam rem aperiam, eaque ipsa quae ab illo inventore veritatis et quasi architecto beatae vitae dicta sunt explicabo.</p>

  <div class="abs treat" style="left:76px;top:894px">
    <div class="treat-img" role="img" aria-label="Cryolipolysis machine with a relaxed client" style="background:linear-gradient(135deg,#f4f4f4,#d9dbe0)"></div>
    <span class="treat-badge"><svg width="16" height="16" viewBox="0 0 16 16"><path d="M8 1v14M1 8h14M3 3l10 10M13 3L3 13" stroke="#fff" stroke-width="1.6"/></svg></span>
    <h3>Cryolipolysis</h3>
    <p>Sed ut perspiciatis unde omnis iste natus error sit voluptatem accusantium doloremque laudantium</p>
  </div>
  <div class="abs treat" style="left:331px;top:894px">
    <div class="treat-img" role="img" aria-label="Body contouring treatment on hips" style="background:linear-gradient(135deg,#eaf6f0,#e8c9b6)"></div>
    <span class="treat-badge"><svg width="16" height="16" viewBox="0 0 16 16"><path d="M8 1v14M1 8h14M3 3l10 10M13 3L3 13" stroke="#fff" stroke-width="1.6"/></svg></span>
    <h3>Trimflox</h3>
    <p>Sed ut perspiciatis unde omnis iste natus error sit voluptatem accusantium doloremque laudantium</p>
  </div>
  <div class="abs treat" style="left:598px;top:894px">
    <div class="treat-img" role="img" aria-label="Relaxing lymph massage with candles" style="background:linear-gradient(135deg,#c99a62,#7a4a28)"></div>
    <span class="treat-badge"><svg width="16" height="16" viewBox="0 0 16 16"><path d="M8 1v14M1 8h14M3 3l10 10M13 3L3 13" stroke="#fff" stroke-width="1.6"/></svg></span>
    <h3>Lymfemassage</h3>
    <p>Sed ut perspiciatis unde omnis iste natus error sit voluptatem accusantium doloremque laudantium</p>
  </div>
  <div class="abs treat" style="left:872px;top:894px">
    <div class="treat-img" role="img" aria-label="Treatment products applied during a session" style="background:linear-gradient(135deg,#e9c8b2,#5c7fa8)"></div>
    <span class="treat-badge"><svg width="16" height="16" viewBox="0 0 16 16"><path d="M8 1v14M1 8h14M3 3l10 10M13 3L3 13" stroke="#fff" stroke-width="1.6"/></svg></span>
    <h3>Produkter</h3>
    <p>Sed ut perspiciatis unde omnis iste natus error sit voluptatem accusantium doloremque laudantium</p>
  </div>
</section>

<section class="abs welcome">
  <div class="abs welcome-photo" role="img" aria-label="Slim woman in white underwear wrapped by a pink measuring ribbon"></div>
  <h2 class="abs">Welcome To Lirava</h2>
  <p class="abs" style="top:150px">Sed ut perspiciatis unde omnis iste natus error sit voluptatem accusantium doloremque laudantium, totam rem aperiam, eaque ipsa quae ab illo inventore veritatis et quasi architecto beatae vitae dicta sunt explicabo. Nemo enim ipsam voluptatem quia voluptas sit aspernatur</p>
  <p class="abs" style="top:242px">Sed ut perspiciatis unde omnis iste natus error sit voluptatem accusantium doloremque laudantium, totam rem aperiam</p>
  <a class="abs btn" href="#">READ MORE</a>
</section>

<section>
  <h2 class="abs news-title">Latest News</h2>
  <svg class="abs news-nav" width="24" height="14" viewBox="0 0 24 14"><path d="M7 2 L2 7 L7 12 M17 2 L22 7 L17 12" fill="none" stroke="#333" stroke-width="2"/></svg>

  <article class="abs news-item" style="left:98px;top:1856px">
    <div class="news-img" role="img" aria-label="Body treatment being performed" style="background:linear-gradient(135deg,#e9d0bf,#6a86b0)"></div>
    <h4>Nulla at diam ornare, aliquam urna</h4>
    <span class="news-date">JAN 25, 2017</span>
    <p>Nulla at diam ornare, aliquam urna vel, commodo urna. Nam id risus a est luctus consectetur quis eget libero. Suspendisse potenti. Pellentesque habitant morbi tristique senectus</p>
    <span class="news-more">Read More +</span>
  </article>
  <article class="abs news-item" style="left:630px;top:1856px">
    <div class="news-img" role="img" aria-label="Woman holding her waist" style="background:linear-gradient(135deg,#f3f3f3,#e8c4ad)"></div>
    <h4>Nulla at diam ornare, aliquam urna</h4>
    <span class="news-date">JAN 25, 2017</span>
    <p>Nulla at diam ornare, aliquam urna vel, commodo urna. Nam id risus a est luctus consectetur quis eget libero. Suspendisse potenti. Pellentesque habitant morbi tristique senectus</p>
    <span class="news-more">Read More +</span>
  </article>
</section>

<section class="abs ba">
  <h2>før efter</h2>
  <div class="ba-card" style="left:100px;background:linear-gradient(90deg,#b58a6e,#8a9bb0)" role="img" aria-label="Before and after photo of a woman in a bikini"></div>
  <div class="ba-card" style="left:357px;background:linear-gradient(90deg,#d8c7b8,#c9a48e)" role="img" aria-label="Before and after side profile of a woman"></div>
  <div class="ba-card" style="left:612px;background:linear-gradient(90deg,#c89a80,#3a3030)" role="img" aria-label="Before and after belly comparison"></div>
  <div class="ba-card" style="left:864px;background:linear-gradient(90deg,#e0b9a0,#f2f2f2)" role="img" aria-label="Before and after back view comparison"></div>
</section>

<footer class="abs footer">
  <div class="abs f-brand"><span class="brand-dot"></span><span class="brand-name" style="font-size:40px">Lirava</span></div>
  <div class="abs f-tag">Body &amp; Health</div>
  <div class="abs social"><i></i><i></i><i></i><i></i><i></i></div>

  <h4 style="left:329px">Quick Links</h4>
  <ul class="abs links">
    <li>Home</li><li>Lirava</li><li>Behandlinger</li><li>Produkter</li><li>Priser</li><li>Blog</li><li>Kontakt</li>
  </ul>

  <h4 style="left:537px">Sign up for Newsletter</h4>
  <p class="abs news-lead">Sed ut perspiciatis unde omnis iste natus error sit voluptatem accusantium doloremque</p>
  <div class="abs field" style="top:157px">Enter Name</div>
  <div class="abs field" style="top:212px">Enter Email</div>

  <h4 style="left:898px">Contact Us</h4>
  <p class="abs contact">Lirava<br>12 Elmwood Lane&nbsp; Harborvale<br>PA 17999</p>
  <div class="contact-row" style="top:172px">
    <svg width="18" height="18" viewBox="0 0 18 18"><path d="M4 2 L7 2 L8 6 L6 7.5 C7 10 8 11 10.5 12 L12 10 L16 11 L16 14 C16 15 15 16 14 16 C7 16 2 11 2 4 C2 3 3 2 4 2 Z" fill="none" stroke="#6a9a4a" stroke-width="1.4"/></svg>
    Phone : 888-555-0142</div>
  <div class="contact-row" style="top:198px">
    <svg width="18" height="14" viewBox="0 0 18 14"><rect x="1" y="1" width="16" height="12" fill="none" stroke="#6a9a4a" stroke-width="1.4"/><path d="M1 1 L9 8 L17 1" fill="none" stroke="#6a9a4a" stroke-width="1.4"/></svg>
    Email : info@lirava.com</div>
</footer>
<div class="abs subscribe">SUBSCRIBE</div>

<div class="abs bottom">©2017 Lirava .. All Rights Reserved.</div>

</body>
</html>
```